Moravel Aesthetic Doctor

I require an elegant, luxurious looking business card for my aesthetic business. I am a doctor and that will set me aside from competitors. I am planning to provide home and spa based treatments to clients with high expectations. I have attached my logo.

```html
<!DOCTYPE html>
<html lang="en">
<head>
<meta charset="utf-8">
<title>Moravel Aesthetic Doctor – Business Card</title>
<link rel="stylesheet" href="https://fonts.googleapis.com/css2?family=Roboto:ital,wght@0,300;0,400;1,400&family=Josefin+Sans:wght@300;400&display=swap">
<style>
  :root {
    --bg: #b9b9b9;
    --card: #efefef;
    --card-edge: #e2e2e2;
    --ink: #2a2a2a;
    --name-grey: #8a919c;
    --blue: #3c9ad6;
    --blue-deep: #0f66ab;
    --blue-mid: #3f8fc9;
    --pill: #4aa3d8;
    --faint: #dcdcdc;
  }
  * { margin: 0; padding: 0; box-sizing: border-box; }
  html, body { width: 1200px; height: 576px; overflow: hidden; }
  body { background: var(--bg); position: relative; font-family: "Roboto", sans-serif; }

  .card {
    position: absolute;
    top: 138px;
    width: 484px;
    height: 292px;
    border-radius: 10px;
    background: linear-gradient(180deg, #f4f4f4 0%, var(--card) 60%, var(--card-edge) 100%);
    box-shadow: 0 3px 6px rgba(0,0,0,.25);
    overflow: hidden;
  }
  .card--front { left: 81px; }
  .card--back { left: 602px; }

  /* front */
  .brand-mark {
    position: absolute; left: 84px; top: 60px;
    width: 92px; height: 92px; border-radius: 50%;
    border: 2px solid var(--name-grey);
  }
  .brand-name {
    position: absolute; left: 196px; top: 66px;
    font-family: "Josefin Sans", sans-serif; font-weight: 300;
    color: var(--name-grey); line-height: 1;
  }
  .brand-name__main { display: block; font-size: 44px; letter-spacing: 2px; }
  .brand-name__sub { display: block; font-size: 19px; letter-spacing: 1.6px; margin-top: 8px; }

  .services {
    position: absolute; left: 0; right: 0; top: 195px;
    text-align: center; font-size: 13px; color: var(--ink); line-height: 19px;
  }
  .services .sep { color: var(--blue); margin: 0 7px; }

  .front-band {
    position: absolute; left: 0; right: 0; top: 240px; height: 33px;
    background: linear-gradient(90deg, var(--blue-deep) 0%, var(--blue-mid) 50%, var(--blue-deep) 100%);
    color: #fff; text-align: center;
    font-family: "Josefin Sans", sans-serif; font-size: 13.5px; letter-spacing: .8px;
    line-height: 35px;
  }

  /* back */
  .faint-circle {
    position: absolute; right: -30px; top: -10px;
    width: 250px; height: 250px; border-radius: 50%;
    background: var(--faint); opacity: .7;
  }
  .doctor-name {
    position: absolute; left: 27px; top: 44px;
    font-size: 20px; font-weight: 400; color: var(--ink);
  }
  .credentials {
    position: absolute; left: 27px; top: 72px;
    font-size: 10px; font-style: italic; color: var(--blue);
  }
  .diploma {
    position: absolute; left: 27px; top: 86px;
    font-size: 13px; color: var(--blue);
  }
  .contacts { position: absolute; left: 27px; top: 186px; list-style: none; }
  .contacts li {
    display: flex; align-items: center; gap: 9px;
    font-size: 13px; color: var(--ink); height: 18px;
  }
  .contacts svg { width: 11px; height: 11px; fill: var(--blue); }
  .follow {
    position: absolute; left: 27px; top: 246px;
    display: flex; align-items: center; gap: 6px;
    font-size: 13px; color: var(--ink);
  }
  .follow .dot { width: 12px; height: 12px; border-radius: 50%; background: var(--blue); }
  .follow .dot:first-of-type { margin-left: 4px; }
  .back-pill {
    position: absolute; left: 170px; right: 0; top: 242px; height: 26px;
    background: var(--pill); border-radius: 13px 0 0 13px;
    color: #fff; font-size: 13.5px; text-align: center; line-height: 26px;
    padding-right: 60px;
  }
</style>
</head>
<body>

<section class="card card--front" aria-label="Business card front">
  <div class="brand-mark"></div>
  <div class="brand-name">
    <span class="brand-name__main">MORAVEL</span>
    <span class="brand-name__sub">AESTHETIC DOCTOR</span>
  </div>
  <div class="services">
    <div>Dermal Injectables<span class="sep">|</span>Plasma Facials<span class="sep">|</span>Microneedling</div>
    <div>Skin Boosters<span class="sep">|</span>Excessive Sweating</div>
  </div>
  <div class="front-band">HOME AND SPA BASED TREATMENTS</div>
</section>

<section class="card card--back" aria-label="Business card back">
  <div class="faint-circle"></div>
  <h1 class="doctor-name">Dr Elena Marsh</h1>
  <p class="credentials">MRCPCH MD</p>
  <p class="diploma">Australasian Diploma of Aesthetic Medicine</p>
  <ul class="contacts">
    <li>
      <svg viewBox="0 0 24 24" aria-hidden="true"><path d="M6.6 10.8a15 15 0 0 0 6.6 6.6l2.2-2.2c.3-.3.7-.4 1-.2 1.1.4 2.3.6 3.6.6.6 0 1 .4 1 1V20c0 .6-.4 1-1 1A17 17 0 0 1 3 4c0-.6.4-1 1-1h3.5c.6 0 1 .4 1 1 0 1.3.2 2.5.6 3.6.1.3 0 .7-.2 1z"/></svg>
      0800 555 014
    </li>
    <li>
      <svg viewBox="0 0 24 24" aria-hidden="true"><path d="M2 5h20v14H2z M4 7v.5l8 5 8-5V7l-8 5z" fill-rule="evenodd"/></svg>
      elena@moravel.co.nz
    </li>
    <li>
      <svg viewBox="0 0 24 24" aria-hidden="true"><path d="M12 2a10 10 0 1 0 0 20 10 10 0 0 0 0-20zm6.9 6h-3a15 15 0 0 0-1.3-3.9A8 8 0 0 1 18.9 8zM12 4c.8 1.2 1.5 2.5 1.9 4h-3.8c.4-1.5 1.1-2.8 1.9-4zM4.3 14a8 8 0 0 1 0-4h3.4a16 16 0 0 0 0 4zm.8 2h3a15 15 0 0 0 1.3 3.9A8 8 0 0 1 5.1 16zm3-8h-3a8 8 0 0 1 4.3-3.9C8.8 5.3 8.4 6.6 8.1 8zM12 20c-.8-1.2-1.5-2.5-1.9-4h3.8c-.4 1.5-1.1 2.8-1.9 4zm2.3-6H9.7a14 14 0 0 1 0-4h4.6a14 14 0 0 1 0 4zm.3 5.9c.6-1.2 1-2.5 1.3-3.9h3a8 8 0 0 1-4.3 3.9zm1.7-5.9a16 16 0 0 0 0-4h3.4a8 8 0 0 1 0 4z"/></svg>
      www.moravel.co.nz
    </li>
  </ul>
  <div class="follow">Follow us on:<span class="dot"></span><span class="dot"></span></div>
  <div class="back-pill">Home &amp; Spa Based Treatments</div>
</section>

</body>
</html>
```